Pebblebrook Plots - Online-only garden installation company

Online-only garden installation company. Our demographic is middle aged / suburban women, and we anticipate Facebook driving traffic to this website, as well as referrals from garden centers. The website must be very simple in design and function.

All orders will be placed through the website, including size of garden (3 options), location in yard, payment, and scheduling of installation date.

The website should employ a 3 step process:

Step 1: Select garden size. Either an 4' X 4', 8' X 4', or 12' X 4'.

Step 2: Select a location. We would like to use an online map to look up a US address, then "drag and drop" one of the garden sizes from step 1 to the location the customer would like us to install the garden at their home.

Step 3: Pick an installation date and pay. Using an online calendar the customer will pick a date, and then pay for the installation via credit card.

The website will be linked to an email account, PebblebrookPlots@mailvale.com to inform us of orders placed.

Target Market(s)

Our demographic is middle aged / suburban women, and we anticipate Facebook driving traffic to this website, as well as referrals from garden centers.

Industry/Entity Type

Coding

Number of Pages Required

Requirements
Must have
• Scheduling and payment options.

```html
<!DOCTYPE html>
<html lang="en">
<head>
<meta charset="utf-8">
<title>Pebblebrook Plots – Garden Installation</title>
<link href="https://fonts.googleapis.com/css2?family=Roboto:wght@400;500;700&family=Roboto+Condensed:wght@400;700&family=Noto+Serif:ital@1&display=swap" rel="stylesheet">
<style>
:root{
  --green:#3a7d2c;
  --green-dark:#2f6a23;
  --orange:#ea6a35;
  --text:#333;
  --muted:#666;
  --light:#f4f4f4;
  --panel:#e6eaf1;
  --line:#ddd;
  --white:#fff;
}
*{box-sizing:border-box;margin:0;padding:0}
html,body{width:1200px;height:3237px;overflow:hidden}
body{position:relative;background:var(--white);font-family:'Roboto',sans-serif;color:var(--text)}
.abs{position:absolute}
.heading{font-family:'Roboto Condensed',sans-serif;font-weight:700;text-transform:uppercase;color:#222}
.serif-sub{font-family:'Noto Serif',serif;font-style:italic;font-size:14px;color:var(--muted)}
.center{left:0;width:1200px;text-align:center}

/* top bar */
.topbar{top:0;left:0;width:1200px;height:30px;background:var(--green);color:var(--white);font-size:12px}
.topbar span{position:absolute;top:8px}
.topbar svg{vertical-align:-2px;margin-right:6px}
.social-dot{position:absolute;top:9px;width:12px;height:12px;border-radius:50%;background:#8fbf80}
/* header */
.header{top:30px;left:0;width:1200px;height:82px;background:var(--white)}
.brand{position:absolute;left:104px;top:36px;display:flex;align-items:center;gap:10px;font-family:'Roboto Condensed',sans-serif;font-weight:700;font-size:22px;color:var(--green)}
.brand i{display:block;width:18px;height:18px;border-radius:50%;background:var(--orange)}
.nav a{position:absolute;top:34px;font-size:14px;color:#222;text-decoration:none}
/* hero */
.hero{top:112px;left:0;width:1200px;height:445px;background:linear-gradient(180deg,#8fa7ae 0%,#7a8f6a 45%,#4f7a32 75%,#3f6a2a 100%)}
.hero h1{position:absolute;top:125px;font-family:'Roboto Condensed',sans-serif;font-weight:700;font-size:64px;color:var(--white);letter-spacing:1px}
.hero p{position:absolute;top:206px;font-size:17px;color:var(--white);letter-spacing:5px;font-weight:500}
.hero .btn-ghost{position:absolute;left:498px;top:270px;width:205px;height:41px;border:2px solid var(--white);background:rgba(0,0,0,.45);color:var(--white);font-size:15px;line-height:37px;text-align:center}
/* welcome */
.welcome{top:557px;left:0;width:1200px;height:479px;background:var(--light)}
.photo{position:absolute;border:8px solid var(--white);box-shadow:0 2px 6px rgba(0,0,0,.15)}
.welcome h2{position:absolute;left:641px;top:80px;font-family:'Roboto Condensed',sans-serif;font-weight:700;font-size:46px;color:var(--green)}
.welcome h3{position:absolute;left:641px;top:140px;font-family:'Roboto Condensed',sans-serif;font-weight:700;font-size:21px;color:#222}
.welcome .copy{position:absolute;left:641px;top:192px;width:423px;font-size:12.5px;line-height:23px;color:var(--muted);text-align:justify}
.btn-orange{background:var(--orange);color:var(--white);text-align:center}
.welcome .btn-orange{position:absolute;left:641px;top:356px;width:173px;height:39px;line-height:39px;font-size:15px}
/* why choose */
.why-title{top:1090px;font-size:30px}
.why-sub{top:1127px}
.feature{top:1178px;height:119px;border:1px dashed #8cbc7f;background:var(--white);padding:18px 18px}
.feature h4{display:flex;align-items:center;gap:12px;font-size:16px;font-weight:500;color:var(--green);margin-bottom:12px}
.feature p{font-size:12px;line-height:21px;color:var(--muted);padding-left:2px}
.rule{top:1353px;left:97px;width:1004px;height:1px;background:var(--line)}
/* how it works */
.how-title{left:97px;top:1400px;font-size:30px}
.how-sub{left:97px;top:1440px}
.step-num{left:97px;width:53px;height:53px;border-radius:50%;background:var(--green);color:var(--white);font-size:22px;font-weight:700;text-align:center;line-height:53px}
.step{left:173px;width:440px}
.step h5{font-size:20px;font-weight:400;color:#222;margin-bottom:6px}
.step p{font-size:12px;line-height:20px;color:var(--muted)}
.quote{top:1405px;left:686px;width:363px;height:321px;background:var(--panel);padding:22px 28px}
.quote h6{font-family:'Noto Serif',serif;font-weight:400;font-size:19px;color:#444;margin-bottom:26px}
.field{position:absolute;height:34px;background:var(--white);border:1px solid #d7dce4;font-size:11px;color:#999;padding:0 12px;line-height:32px}
.field svg{position:absolute;right:10px;top:11px}
.quote .btn-orange{position:absolute;left:28px;top:268px;width:90px;height:32px;line-height:32px;font-size:12px}
/* testimonial */
.testi{top:1787px;left:0;width:1200px;height:386px;background:var(--orange)}
.testi h2{position:absolute;top:52px;font-family:'Roboto Condensed',sans-serif;font-weight:700;font-size:28px;color:var(--white)}
.avatar{position:absolute;left:563px;top:113px;width:74px;height:74px;border-radius:50%;border:4px solid var(--white);background:#d8c8bb}
.testi .said{position:absolute;top:210px;left:350px;width:500px;text-align:center;font-size:12px;line-height:22px;color:var(--white)}
.testi .who{position:absolute;top:292px;font-size:15px;font-weight:500;color:var(--white)}
.testi .role{position:absolute;top:313px;font-size:11px;color:#ffe0d0}
/* blog */
.blog-title{top:2230px;font-size:30px}
.post-img{top:2294px;width:311px;height:162px}
.post h4{font-size:16px;font-weight:700;color:#222;margin-bottom:10px}
.post p{font-size:12px;line-height:19px;color:var(--muted)}
/* map */
.map{top:2631px;left:0;width:1200px;height:308px;background:linear-gradient(135deg,#e9ebe8,#dfe3df)}
/* footer */
.foot h5{font-size:16px;font-weight:700;color:#222;text-transform:uppercase;margin-bottom:22px}
.foot p{font-size:12px;line-height:22px;color:var(--muted);text-align:justify}
.foot ul{list-style:none}
.foot li{font-size:12px;line-height:22px;color:var(--muted)}
.readmore{color:var(--green);font-size:13px;margin-top:10px;display:block}
.join{display:inline-block;margin-top:16px;border:1px solid #999;padding:6px 18px;font-size:12px;color:#444}
.ring{display:inline-block;width:24px;height:24px;border-radius:50%;border:1px solid #999;margin-right:4px}
.copyright{top:3190px;left:0;width:1200px;height:47px;background:#efefef;font-size:12px;color:var(--muted);text-align:center;line-height:47px}
</style>
</head>
<body>

<div class="abs topbar">
  <span style="left:520px"><svg width="11" height="11" viewBox="0 0 24 24"><path fill="#fff" d="M6.6 10.8a15 15 0 0 0 6.6 6.6l2.2-2.2c.3-.3.7-.4 1-.2 1.1.4 2.3.6 3.6.6.6 0 1 .4 1 1V20c0 .6-.4 1-1 1A17 17 0 0 1 3 4c0-.6.4-1 1-1h3.5c.6 0 1 .4 1 1 0 1.3.2 2.5.6 3.6.1.3 0 .7-.2 1z"/></svg>Call us on : 555 018 4420</span>
  <span style="left:714px"><svg width="12" height="10" viewBox="0 0 24 18"><rect x="1" y="1" width="22" height="16" fill="none" stroke="#fff" stroke-width="2"/><path d="M1 1l11 9 11-9" fill="none" stroke="#fff" stroke-width="2"/></svg>Mail us on : PebblebrookPlots@mailvale.com</span>
  <i class="social-dot" style="left:968px"></i><i class="social-dot" style="left:995px"></i><i class="social-dot" style="left:1022px"></i><i class="social-dot" style="left:1049px"></i><i class="social-dot" style="left:1076px"></i>
</div>

<header class="abs header">
  <div class="brand"><i></i>Pebblebrook Plots</div>
  <nav class="nav">
    <a style="left:383px">HOME</a><a style="left:467px">ABOUT US</a><a style="left:577px">SERVICES</a><a style="left:690px">GARDENERS</a><a style="left:808px">GALLERY</a><a style="left:911px">BLOG</a><a style="left:990px">CONTACT</a>
    <span class="abs" style="left:1066px;top:34px;width:1px;height:16px;background:#333"></span>
    <svg class="abs" style="left:1083px;top:35px" width="14" height="14" viewBox="0 0 24 24"><circle cx="10" cy="10" r="7" fill="none" stroke="#222" stroke-width="3"/><path d="M15 15l7 7" stroke="#222" stroke-width="3"/></svg>
  </nav>
</header>

<section class="abs hero" role="img" aria-label="Suburban backyard with green lawn, garden beds and stone path">
  <h1 class="center" style="text-align:center">PEBBLEBROOK PLOTS</h1>
  <p class="center" style="text-align:center">WE ARE A GARDEN INSTALLATION COMPANY</p>
  <div class="btn-ghost">GET INSTALLATION</div>
</section>

<section class="abs welcome">
  <div class="photo" role="img" aria-label="Wooden deck and fence" style="left:101px;top:129px;width:281px;height:289px;background:linear-gradient(160deg,#9a6a48,#6b4a35 60%,#4e3b30)"></div>
  <div class="photo" role="img" aria-label="Gardener laying turf on soil" style="left:306px;top:62px;width:251px;height:292px;background:linear-gradient(180deg,#5f7a3b,#7a6146 55%,#5a4634)"></div>
  <h2>WELCOME TO</h2>
  <h3>OUR GARDEN INSTALLATION COMPANY</h3>
  <p class="copy">Lorem is a long established fact that a reader will be distracted by the readable content of a page when looking at its layout. The point of using Lorem Ipsum is that it has a more-or-less normal distribution of letters, as opposed to using 'Content here, content here', making it look like readable English. Many desktop publishing packages .</p>
  <div class="btn-orange">Get Free Installation</div>
</section>

<h2 class="abs heading center why-title">Why Choose Us</h2>
<p class="abs serif-sub center why-sub">Sed ut perspiciatis unde omnis iste natus error Sed perspiciatis</p>

<div class="abs feature" style="left:97px;width:320px">
  <h4><svg width="24" height="22" viewBox="0 0 24 22"><rect x="1" y="5" width="22" height="16" rx="2" fill="#3a7d2c"/><rect x="8" y="1" width="8" height="5" fill="none" stroke="#3a7d2c" stroke-width="2"/></svg>We are 20 Years of experience</h4>
  <p>Sed ut perspiciatis unde omnis iste natus error sit to voluptatem accusatm doloremque laudantium</p>
</div>
<div class="abs feature" style="left:442px;width:315px">
  <h4><svg width="22" height="22" viewBox="0 0 24 24"><rect x="1" y="10" width="5" height="12" fill="#3a7d2c"/><path d="M8 10l5-8c2 0 3 1 2.5 3L14 9h7c1 0 2 1 1.8 2l-2 9c-.2.8-1 1.5-2 1.5H8z" fill="#3a7d2c"/></svg>We completed 200+ projects</h4>
  <p>Sed ut perspiciatis unde omnis iste natus error sit to voluptatem accusatm doloremque laudantium</p>
</div>
<div class="abs feature" style="left:786px;width:315px">
  <h4><svg width="26" height="22" viewBox="0 0 26 22"><path d="M2 12l6-7h5l5 5 6-4v6l-8 8H9z" fill="#3a7d2c"/></svg>Professional and convenient</h4>
  <p>Sed ut perspiciatis unde omnis iste natus error sit to voluptatem accusatm doloremque laudantium</p>
</div>

<div class="abs rule"></div>

<h2 class="abs heading how-title">How It Works</h2>
<p class="abs serif-sub how-sub">Sed ut perspiciatis unde omnis iste natus error Sed perspiciatis</p>

<div class="abs step-num" style="top:1489px">1</div>
<div class="abs step" style="top:1487px"><h5>Select garden size.</h5><p>Select the size of the garden by Either an 4' X 4', 8' X 4', or 12' X 4'.</p></div>
<div class="abs step-num" style="top:1571px">2</div>
<div class="abs step" style="top:1565px"><h5>Select a location.</h5><p>We would like to use an online map to look up a US address,then "drag and drop" one of the garden sizes from step 1 to the location</p></div>
<div class="abs step-num" style="top:1668px">3</div>
<div class="abs step" style="top:1662px"><h5>Pick an installation date and pay.</h5><p>Using an online calendar the customer will pick a date, and then pay for the installation via credit card.</p></div>

<aside class="abs quote">
  <h6>GET A QUOTE</h6>
  <div class="field" style="left:28px;top:71px;width:152px">Name<svg width="11" height="11" viewBox="0 0 24 24"><circle cx="12" cy="7" r="5" fill="#bbb"/><path d="M2 23c0-6 4-9 10-9s10 3 10 9z" fill="#bbb"/></svg></div>
  <div class="field" style="left:188px;top:71px;width:147px">Size of garden<svg width="9" height="9" viewBox="0 0 24 24"><path d="M4 8l8 8 8-8" fill="none" stroke="#bbb" stroke-width="3"/></svg></div>
  <div class="field" style="left:28px;top:119px;width:307px">location in yard<svg width="10" height="12" viewBox="0 0 20 24"><path d="M10 0a8 8 0 0 0-8 8c0 6 8 16 8 16s8-10 8-16a8 8 0 0 0-8-8z" fill="#bbb"/><circle cx="10" cy="8" r="3" fill="#fff"/></svg></div>
  <div class="field" style="left:28px;top:167px;width:307px">payment<svg width="13" height="10" viewBox="0 0 26 18"><rect x="1" y="1" width="24" height="16" rx="2" fill="none" stroke="#bbb" stroke-width="2"/><rect x="1" y="5" width="24" height="3" fill="#bbb"/></svg></div>
  <div class="field" style="left:28px;top:215px;width:307px">scheduling of installation date<svg width="11" height="11" viewBox="0 0 24 24"><rect x="2" y="4" width="20" height="18" fill="none" stroke="#bbb" stroke-width="2.5"/><rect x="2" y="4" width="20" height="5" fill="#bbb"/></svg></div>
  <div class="btn-orange">SEND NOW</div>
</aside>

<section class="abs testi">
  <h2 class="center" style="text-align:center">WHAT OUR CLIENT SAYS</h2>
  <div class="avatar" role="img" aria-label="Client portrait"></div>
  <p class="said">I must explain to you how all this mistaken idea of denouncing pleasure and praising pain was born and I will give you a complete account of the system, and expound the actual teachings of the great explorer of the truth</p>
  <p class="who center" style="text-align:center">Marla Quinby</p>
  <p class="role center" style="text-align:center">Installer</p>
</section>

<h2 class="abs heading center blog-title">Our Recent Blog Post</h2>
<div class="abs post-img" role="img" aria-label="Hands planting a seedling in soil" style="left:99px;background:linear-gradient(160deg,#8fb0b5,#6a5238 60%,#3f2e22)"></div>
<div class="abs post-img" role="img" aria-label="Patio furniture on a wooden deck" style="left:445px;background:linear-gradient(170deg,#5f7f3a,#a55a2f 55%,#7a3d1f)"></div>
<div class="abs post-img" role="img" aria-label="Landscaped lawn with flower beds and trees" style="left:790px;background:linear-gradient(180deg,#6fa0d4,#4a7a35 45%,#5ea43a)"></div>
<article class="abs post" style="left:99px;top:2476px;width:311px"><h4>SED PERSPICIATIS UNDE OMNIS</h4><p>Lorem ipsum dolor sit amet, consectetuer. Proin gravida nibh vel velit auctor aliquet. the far Aenean sollicitudi ravida.Lorem ipsum dolor sit amet.</p></article>
<article class="abs post" style="left:445px;top:2476px;width:311px"><h4>SED PERSPICIATIS UNDE OMNIS</h4><p>Lorem ipsum dolor sit amet, consectetuer. Proin gravida nibh vel velit auctor aliquet. the far Aenean sollicitudi ravida.Lorem ipsum dolor sit amet.</p></article>
<article class="abs post" style="left:790px;top:2476px;width:311px"><h4>SED PERSPICIATIS UNDE OMNIS</h4><p>Lorem ipsum dolor sit amet, consectetuer. Proin gravida nibh vel velit auctor aliquet. the far Aenean sollicitudi ravida.Lorem ipsum dolor sit amet.</p></article>

<div class="abs map" role="img" aria-label="Regional map showing installation locations"></div>

<footer>
  <div class="abs foot" style="left:97px;top:2985px;width:290px">
    <h5>About Us</h5>
    <p>At vero eos et accusamus et iusto odio dignissimos ducimus qui blanditiis praesentium voluptatum deleniti atque corrupti quos dolores</p>
    <span class="readmore">Read More &gt;&gt;</span>
  </div>
  <div class="abs foot" style="left:453px;top:2985px;width:150px">
    <h5>Site Map</h5>
    <ul><li>About us</li><li>Our Process</li><li>Our Work</li><li>Resources</li><li>Case Studies</li></ul>
  </div>
  <div class="abs foot" style="left:630px;top:2985px;width:230px">
    <h5>Work With Us</h5>
    <p>At vero eos et accusamus et iusto odio dignissimos ducimus qui</p>
    <span class="join">Join Us</span>
  </div>
  <div class="abs foot" style="left:909px;top:2985px;width:200px">
    <h5>Connect With Us</h5>
    <span class="ring"></span><span class="ring"></span><span class="ring"></span><span class="ring"></span><span class="ring"></span><span class="ring"></span>
  </div>
  <div class="abs copyright">Copyrights@2017Pebblebrook Plots , all rights Reserved</div>
</footer>

</body>
</html>
```